KVOR Individual and Corporate Development Business Card Design

KVOR needs a business card design that is aligned with it's values and targetted markets. Coherent Lattice of Adaptive Reasoning Method's self diagnosis model and tools, which can be used for personal improvement and team/business performance enhancement, is based on the learnings of over 20 years of medical practitioning. KVOR supercharges personal effectiveness and awareness to also increase team and business performance.

The targetted markets are high performance individuals and teams who aspire seek to enhance their capabilities and achieve their absolute best potential.

Look and feel for the business card design we are looking for is high technology, premium, fresh, new and medical.

Target Market(s)

Industry/Entity Type

Business Consultant

Contact Information for Business Card

Logo, Full Name, Title, Phone number, Email, company name, Address,

Font styles to use
Sans Serif

Requirements
Must have
• Tag line: Elevating Potential for Focused and Driven Achievers
• Please use same colours as the logo.

```html
<!DOCTYPE html>
<html lang="en">
<head>
<meta charset="utf-8">
<title>KVOR Business Card</title>
<link rel="stylesheet" href="https://fonts.googleapis.com/css2?family=Roboto:ital,wght@0,400;0,500;0,700;1,400&family=Roboto+Condensed:wght@400;700&display=swap">
<style>
  :root {
    --backdrop: #2a2a2c;
    --card-light: #fbfbfb;
    --card-dark: #2c2c2e;
    --teal: #1fb3c8;
    --ink-grey: #5a5a5a;
    --rule-grey: #8a8a8a;
    --brand-rule: #c9c9c9;
    --white: #ffffff;
  }
  * { margin: 0; padding: 0; box-sizing: border-box; }
  html, body { width: 1200px; height: 900px; overflow: hidden; }
  body {
    background: var(--backdrop);
    font-family: "Roboto", Arial, sans-serif;
    position: relative;
  }
  .card {
    position: absolute;
    left: 290px;
    width: 620px;
    height: 354px;
    border-radius: 3px;
    box-shadow: 0 6px 18px rgba(0,0,0,0.45);
  }
  .card-front { top: 76px; background: var(--card-light); }
  .card-back { top: 470px; background: var(--card-dark); color: var(--white); }

  .brand {
    position: absolute;
    left: 0; right: 0; top: 110px;
    display: flex; align-items: center; justify-content: center; gap: 14px;
  }
  .brand-mark { width: 22px; height: 22px; border-radius: 50%; background: var(--teal); }
  .brand-name {
    font-weight: 700;
    font-size: 64px;
    letter-spacing: 4px;
    color: var(--teal);
    line-height: 1;
  }
  .brand-rule {
    position: absolute; left: 190px; right: 190px; top: 196px;
    height: 1px; background: var(--brand-rule);
  }
  .tagline {
    position: absolute; left: 0; right: 0; top: 236px;
    text-align: center;
    font-style: italic;
    font-size: 16px;
    color: var(--ink-grey);
    letter-spacing: 0.2px;
  }

  .person {
    position: absolute; right: 346px; top: 110px;
    text-align: right;
  }
  .person-name {
    font-family: "Roboto Condensed", Arial, sans-serif;
    font-weight: 700;
    font-size: 34px;
    color: var(--teal);
    line-height: 1;
  }
  .person-title {
    font-family: "Roboto Condensed", Arial, sans-serif;
    font-size: 17px;
    margin-top: 6px;
    letter-spacing: 0.4px;
  }
  .divider {
    position: absolute; left: 290px; top: 94px;
    width: 1px; height: 128px;
    background: linear-gradient(to bottom, transparent, var(--rule-grey) 20%, var(--rule-grey) 80%, transparent);
  }
  .company {
    position: absolute; left: 312px; top: 98px; width: 280px;
  }
  .company-name {
    font-weight: 700; font-size: 15px; line-height: 1.2; margin-bottom: 10px;
  }
  .contact-row {
    display: flex; align-items: center; gap: 8px;
    font-size: 16px; line-height: 1.45;
  }
  .icon { width: 14px; height: 14px; fill: var(--teal); flex: none; }
  .icon-pin { width: 16px; height: 18px; }
  .address {
    position: absolute; left: 150px; top: 268px;
    display: flex; align-items: center; gap: 8px;
    font-size: 17px; letter-spacing: 0.3px;
  }
</style>
</head>
<body>
  <section class="card card-front">
    <div class="brand">
      <span class="brand-mark"></span>
      <span class="brand-name">KVOR</span>
    </div>
    <div class="brand-rule"></div>
    <p class="tagline">Elevating Potential for Focused and Driven Achievers</p>
  </section>

  <section class="card card-back">
    <div class="person">
      <div class="person-name">DANIEL REYES</div>
      <div class="person-title">CEO/FOUNDER</div>
    </div>
    <div class="divider"></div>
    <div class="company">
      <div class="company-name">Coherent Lattice of Adaptive<br>Reasoning Method</div>
      <div class="contact-row">
        <svg class="icon" viewBox="0 0 24 24"><path d="M6.6 10.8a15.2 15.2 0 0 0 6.6 6.6l2.2-2.2a1 1 0 0 1 1-.25 11.4 11.4 0 0 0 3.6.57 1 1 0 0 1 1 1V20a1 1 0 0 1-1 1A17 17 0 0 1 3 4a1 1 0 0 1 1-1h3.5a1 1 0 0 1 1 1c0 1.25.2 2.45.57 3.57a1 1 0 0 1-.25 1z"/></svg>
        <span>555 204 7316</span>
      </div>
      <div class="contact-row">
        <svg class="icon" viewBox="0 0 24 24"><path d="M2 6.5 12 13l10-6.5V19H2z"/><path d="M2 5h20l-10 6.5z"/></svg>
        <span>hello@kvorgroup.com</span>
      </div>
      <div class="contact-row">
        <svg class="icon" viewBox="0 0 24 24"><circle cx="12" cy="12" r="10"/><path d="M2 12h20M12 2c3 3 3 17 0 20M12 2c-3 3-3 17 0 20" fill="none" stroke="var(--card-dark)" stroke-width="1.4"/></svg>
        <span>www.kvorgroup.com</span>
      </div>
    </div>
    <div class="address">
      <svg class="icon icon-pin" viewBox="0 0 24 24"><path d="M12 2a7 7 0 0 0-7 7c0 5 7 13 7 13s7-8 7-13a7 7 0 0 0-7-7zm0 9.5A2.5 2.5 0 1 1 12 6.5a2.5 2.5 0 0 1 0 5z"/></svg>
      <span>1420 Harbor View Road, Juneau, Alaska 99801</span>
    </div>
  </section>
</body>
</html>
```